"Harbor Builders" is a residential building company and needs a new business card design and may re

We would like a redesign based on the existing logo, and would like to see a new font as well. We are bespoke home builders who build sustainable energy efficient homes.

Industry/Entity Type

Construction

Contact Information for Business Card

Business card size 40mm x 90mm

Colors

Designer to choose colors to be used in the design.

```html
<!DOCTYPE html>
<html lang="en">
<head>
<meta charset="utf-8">
<title>Harbor Builders — Business Card</title>
<link rel="stylesheet" href="https://fonts.googleapis.com/css2?family=Open+Sans:wght@600&family=Roboto:wght@400;500&family=Roboto+Condensed:wght@500&display=swap">
<style>
  :root {
    --page-bg: #e9e6e1;
    --card-white: #f3f3f3;
    --ink: #1d1d1d;
    --ink-soft: #4a4a4a;
    --rule: #8a8a8a;
    --lime: #a8c834;
    --band-black: #0c0c0c;
    --back-black: #1a1b1c;
    --back-ghost: #0d0d0e;
    --back-url: #3a3b3d;
    --band-text: #e6e6e6;
  }
  * { margin: 0; padding: 0; box-sizing: border-box; }
  html, body { width: 1200px; height: 960px; overflow: hidden; }
  body { background: var(--page-bg); position: relative; font-family: "Roboto", Arial, sans-serif; }

  .card { position: absolute; width: 600px; height: 342px; box-shadow: 0 6px 14px rgba(0,0,0,.35); overflow: hidden; }

  .card-front { left: 302px; top: 130px; background: var(--card-white); color: var(--ink-soft); }
  .brand { position: absolute; right: 58px; top: 40px; display: flex; align-items: center; gap: 12px; }
  .brand-square { width: 26px; height: 26px; background: var(--lime); }
  .brand-name { font-family: "Open Sans", Arial, sans-serif; font-weight: 600; font-size: 28px; color: var(--ink); letter-spacing: -0.5px; }

  .holder-name { position: absolute; left: 29px; top: 156px; font-family: "Roboto Condensed", Arial, sans-serif; font-weight: 500; font-size: 21px; color: var(--ink); }
  .divider { position: absolute; left: 29px; right: 30px; top: 188px; height: 1px; background: var(--rule); }

  .credentials { position: absolute; left: 30px; top: 198px; font-size: 14.5px; line-height: 18px; }
  .contact { position: absolute; left: 30px; top: 239px; font-size: 14.5px; line-height: 19px; }
  .contact li { list-style: none; display: flex; align-items: center; gap: 8px; }
  .contact svg { width: 14px; height: 14px; fill: var(--ink); }

  .address { position: absolute; right: 30px; top: 202px; text-align: right; font-size: 14.5px; line-height: 18px; }
  .address .company { font-weight: 500; color: var(--ink-soft); }

  .band { position: absolute; left: 0; right: 0; bottom: 0; height: 32px; background: var(--band-black); }
  .band-accent { position: absolute; left: 0; top: 0; width: 150px; height: 100%; background: var(--lime); }
  .band-square { position: absolute; left: 152px; top: 3px; width: 26px; height: 26px; background: var(--lime); }
  .band-url { position: absolute; right: 64px; top: 7px; font-style: italic; font-size: 14px; letter-spacing: 2.6px; color: var(--band-text); }

  .card-back { left: 300px; top: 488px; background: var(--back-black); }
  .back-name { position: absolute; left: 50px; top: 222px; font-family: "Open Sans", Arial, sans-serif; font-weight: 600; font-size: 44px; color: var(--back-ghost); letter-spacing: -1px; }
  .back-url { position: absolute; left: 51px; top: 304px; font-size: 14px; color: var(--back-url); }
</style>
</head>
<body>
  <section class="card card-front" aria-label="Business card front">
    <div class="brand"><span class="brand-square"></span><span class="brand-name">harbor builders</span></div>
    <h1 class="holder-name">DANIEL MOREAU</h1>
    <div class="divider"></div>
    <p class="credentials">Registration 30471<br>ABN: 42 305 618 774</p>
    <ul class="contact">
      <li><svg viewBox="0 0 14 14"><path d="M4 0h6a1 1 0 0 1 1 1v12a1 1 0 0 1-1 1H4a1 1 0 0 1-1-1V1a1 1 0 0 1 1-1zm.5 1.5v9h5v-9zM7 11.4a.8.8 0 1 0 0 1.6.8.8 0 0 0 0-1.6z"/></svg>0412 583 907</li>
      <li><svg viewBox="0 0 14 14"><path d="M1 3.5h12v7H1zm1 .8L7 8l5-3.7V4H2z"/></svg>daniel@harborbuilders.com.au</li>
    </ul>
    <p class="address"><span class="company">Harbor Builders Pty Ltd</span><br>PO Box 2187<br>Riverside<br>LPO Eastfield WA 6099</p>
    <div class="band">
      <span class="band-accent"></span>
      <span class="band-square"></span>
      <span class="band-url">www.harborbuilders.com.au</span>
    </div>
  </section>

  <section class="card card-back" aria-label="Business card back">
    <p class="back-name">harbor builders</p>
    <p class="back-url">www.harborbuilders.com.au</p>
  </section>
</body>
</html>
```